Online Home Automation business needs business card design

New business starting up that sells home-automation products in Australia. Business card needs to look very polished and professional. The business name is "Pike Automation".
Updates

Thank you all for the great designs, We are really impressed. We are in the process of deciding on a design but keep the designs coming in.

Industry/Entity Type

Business

```html
<!DOCTYPE html>
<html lang="en">
<head>
<meta charset="utf-8">
<title>Pike Automation — Business Card</title>
<link href="https://fonts.googleapis.com/css2?family=Carlito:wght@400;700&family=Didact+Gothic&display=swap" rel="stylesheet">
<style>
  :root {
    --paper: #ffffff;
    --ink: #111111;
    --frame: #1a1a1a;
    --swoosh: #e4e4e4;
    --band-light: #ffffff;
    --band-dark: #dcdcdc;
    --accent: #e8141b;
    --accent-edge: #6a0a0a;
  }
  * { box-sizing: border-box; margin: 0; padding: 0; }
  html, body { width: 914px; height: 1200px; overflow: hidden; background: var(--paper); }
  .sheet { position: relative; width: 914px; height: 1200px; font-family: "Carlito", sans-serif; color: var(--ink); }
  .side-label {
    position: absolute; font-family: Arial, "Helvetica", sans-serif; font-size: 38px;
    color: var(--ink); transform: translateX(-50%); letter-spacing: 0.5px;
  }
  .side-label--front { left: 433px; top: 128px; }
  .side-label--back { left: 449px; top: 1012px; }
  .card {
    position: absolute; left: 114px; width: 673px; height: 384px;
    border: 1px solid var(--frame); background: var(--paper); overflow: hidden;
  }
  .card--front { top: 175px; }
  .card--back { top: 621px; }
  .card__art { position: absolute; inset: 0; width: 100%; height: 100%; }
  .brand { position: absolute; display: flex; align-items: center; }
  .brand__dot { border-radius: 50%; background: var(--ink); flex: none; }
  .brand__name { font-family: "Didact Gothic", sans-serif; color: var(--ink); line-height: 0.95; }
  .brand__name span { display: block; }
  .card--front .brand { left: 244px; top: 25px; }
  .card--front .brand__dot { width: 100px; height: 100px; margin-right: 32px; }
  .card--front .brand__first { font-size: 62px; }
  .card--front .brand__second { font-size: 42px; }
  .card--back .brand { left: 311px; top: 25px; }
  .card--back .brand__dot { width: 86px; height: 86px; margin-right: 27px; }
  .card--back .brand__first { font-size: 53px; }
  .card--back .brand__second { font-size: 36px; }
  .card__details { position: absolute; left: 19px; top: 247px; font-size: 16.5px; line-height: 23px; }
  .card__details p { text-decoration: underline; }
  .country {
    position: absolute; font-weight: 700; font-size: 23px; color: var(--accent);
    -webkit-text-stroke: 0.6px var(--accent-edge); letter-spacing: 0.2px;
  }
  .card--front .country { right: 9px; bottom: 0px; }
  .card--back .country { left: 49px; bottom: 0px; }
</style>
</head>
<body>
<main class="sheet">
  <div class="side-label side-label--front">FRONT</div>

  <section class="card card--front" aria-label="Card front">
    <svg class="card__art" viewBox="0 0 673 384" aria-hidden="true">
      <defs>
        <linearGradient id="bandFront" x1="0" y1="0" x2="1" y2="0">
          <stop offset="0" stop-color="var(--band-dark)" stop-opacity="0.3"/>
          <stop offset="0.25" stop-color="var(--band-dark)"/>
          <stop offset="1" stop-color="var(--band-light)"/>
        </linearGradient>
      </defs>
      <path d="M140 75 L200 20 L673 20 L673 131 L200 131 Z" fill="url(#bandFront)"/>
      <path d="M2 382 L381 150 C305 225 288 295 356 335 C425 370 540 378 673 383 Z" fill="var(--swoosh)"/>
    </svg>
    <div class="brand">
      <div class="brand__dot"></div>
      <div class="brand__name"><span class="brand__first">Pike</span><span class="brand__second">Automation</span></div>
    </div>
    <div class="card__details">
      <p>SPL :- For selling Home Automation Products.</p>
      <p>Address :-</p>
    </div>
    <div class="country">AUSTRALIA</div>
  </section>

  <section class="card card--back" aria-label="Card back">
    <svg class="card__art" viewBox="0 0 673 384" aria-hidden="true">
      <defs>
        <linearGradient id="bandBack" x1="0" y1="0" x2="1" y2="0">
          <stop offset="0" stop-color="var(--band-dark)" stop-opacity="0.3"/>
          <stop offset="0.25" stop-color="var(--band-dark)"/>
          <stop offset="1" stop-color="var(--band-light)"/>
        </linearGradient>
      </defs>
      <path d="M226 68 L280 20 L673 20 L673 114 L280 114 Z" fill="url(#bandBack)"/>
      <path d="M2 382 L381 150 C305 225 288 295 356 335 C425 370 540 378 673 383 Z" fill="var(--swoosh)"/>
    </svg>
    <div class="brand">
      <div class="brand__dot"></div>
      <div class="brand__name"><span class="brand__first">Pike</span><span class="brand__second">Automation</span></div>
    </div>
    <div class="country">AUSTRALIA</div>
  </section>

  <div class="side-label side-label--back">BACK</div>
</main>
</body>
</html>
```